Dunmore Roofing

Want a professional looking business card

Industry/Entity Type

Business

Contact Information for Business Card

Paul Dunmore ( Owner) paul@dunmoreroofing-example.com, www.dunmoreroofing-example.com, Adress: 4172 Township road 43 Ashford Mills,ON K9X4T2

```html
<!DOCTYPE html>
<html lang="en">
<head>
<meta charset="utf-8">
<title>Dunmore Roofing – Business Card</title>
<link rel="stylesheet" href="https://fonts.googleapis.com/css2?family=Open+Sans:wght@400;600;700&display=swap">
<style>
  :root {
    --backdrop: #3a3330;
    --card: #121314;
    --brand-blue: #2d5aa3;
    --text-light: #e8e8e8;
    --text-muted: #9a9a9a;
    --rule: #cfcfcf;
  }
  * { box-sizing: border-box; margin: 0; padding: 0; }
  html, body {
    width: 1200px; height: 864px; overflow: hidden;
    background: var(--backdrop);
    font-family: "Open Sans", Arial, sans-serif;
  }
  .canvas {
    position: relative; width: 1200px; height: 864px;
    display: flex; align-items: center; justify-content: center; gap: 40px;
  }
  .card {
    position: relative; width: 540px; height: 309px;
    background: var(--card);
    box-shadow: 0 10px 30px rgba(0,0,0,.45);
  }
  /* Front */
  .card-front .brand-name {
    position: absolute; left: 0; right: 0; top: 112px;
    text-align: center;
    color: var(--brand-blue);
    font-weight: 700; font-size: 38px; letter-spacing: 2px;
  }
  .card-front .website {
    position: absolute; left: 0; right: 0; top: 196px;
    text-align: center;
    color: var(--text-muted);
    font-size: 13px; letter-spacing: 4px;
  }
  /* Back */
  .card-back .brand-name {
    position: absolute; right: 34px; top: 66px;
    color: var(--brand-blue); font-weight: 700; font-size: 24px; letter-spacing: 1px;
    text-align: right; line-height: 1.15;
  }
  .holder {
    position: absolute; left: 34px; top: 124px;
  }
  .holder-name {
    color: var(--brand-blue); font-weight: 700; font-size: 17px;
  }
  .holder-title {
    color: var(--text-muted); font-size: 12px; letter-spacing: 1px; margin-top: 1px;
  }
  .title-rule {
    position: absolute; left: 96px; top: 165px; width: 410px; height: 1px;
    background: var(--rule);
  }
  .contact-list {
    position: absolute; left: 34px; top: 178px; list-style: none;
  }
  .contact-list li {
    display: flex; align-items: center; gap: 8px;
    color: var(--text-light); font-size: 13px; line-height: 21px;
  }
  .contact-list svg { width: 11px; height: 11px; fill: var(--brand-blue); flex: none; }
  .address {
    position: absolute; right: 34px; bottom: 22px;
    text-align: right; color: var(--text-light); font-size: 14px; line-height: 20px;
    font-style: normal;
  }
</style>
</head>
<body>
<main class="canvas">
  <section class="card card-front">
    <div class="brand-name">DUNMORE ROOFING</div>
    <div class="website">www.dunmoreroofing-example.com</div>
  </section>

  <section class="card card-back">
    <div class="brand-name">DUNMORE<br>ROOFING</div>
    <div class="holder">
      <div class="holder-name">PAUL DUNMORE</div>
      <div class="holder-title">OWNER</div>
    </div>
    <div class="title-rule"></div>
    <ul class="contact-list">
      <li>
        <svg viewBox="0 0 24 24" aria-hidden="true"><path d="M6.6 10.8a15.1 15.1 0 0 0 6.6 6.6l2.2-2.2c.3-.3.7-.4 1-.2 1.1.4 2.3.6 3.6.6.6 0 1 .4 1 1V20c0 .6-.4 1-1 1A17 17 0 0 1 3 4c0-.6.4-1 1-1h3.5c.6 0 1 .4 1 1 0 1.3.2 2.5.6 3.6.1.3 0 .7-.2 1z"/></svg>
        613 555 0147
      </li>
      <li>
        <svg viewBox="0 0 24 24" aria-hidden="true"><path d="M2 5h20v14H2zM4 7v.5l8 5 8-5V7l-8 5z"/></svg>
        paul@dunmoreroofing-example.com
      </li>
      <li>
        <svg viewBox="0 0 24 24" aria-hidden="true"><path d="M12 2a10 10 0 1 0 0 20 10 10 0 0 0 0-20zm6.9 9h-3a15 15 0 0 0-1.3-6 8 8 0 0 1 4.3 6zM12 4c.9 1.2 1.7 3.7 1.9 7h-3.8c.2-3.3 1-5.8 1.9-7zM9.4 5a15 15 0 0 0-1.3 6h-3a8 8 0 0 1 4.3-6zM5.1 13h3a15 15 0 0 0 1.3 6 8 8 0 0 1-4.3-6zM12 20c-.9-1.2-1.7-3.7-1.9-7h3.8c-.2 3.3-1 5.8-1.9 7zm2.6-1a15 15 0 0 0 1.3-6h3a8 8 0 0 1-4.3 6z"/></svg>
        www.dunmoreroofing-example.com
      </li>
    </ul>
    <address class="address">
      4172 Township road 43<br>
      Ashford Mills, ON K9X4T2
    </address>
  </section>
</main>
</body>
</html>
```